Business Card Design

WE are looking for a premium quality Business Cards for a Law Firm . Copies of our current business card is attached.

Contact Information for Business Card

xyz

```html
<!DOCTYPE html>
<html lang="en">
<head>
<meta charset="utf-8">
<title>Harrowgate Legal — Business Cards</title>
<link rel="stylesheet" href="https://fonts.googleapis.com/css2?family=Tinos:wght@400;700&display=swap">
<style>
  :root {
    --backdrop: #303030;
    --gold: #cdab69;
    --gold-deep: #b8934b;
    --green: #0f2a1c;
    --ink: #111111;
    --paper: #ffffff;
    --serif: "Tinos", "Times New Roman", serif;
  }
  * { box-sizing: border-box; margin: 0; padding: 0; }
  html, body {
    width: 1200px; height: 780px; overflow: hidden;
    background: var(--backdrop);
    font-family: var(--serif);
  }
  .canvas { position: relative; width: 1200px; height: 780px; }
  .card {
    position: absolute; top: 230px;
    width: 560px; height: 320px;
    overflow: hidden;
  }

  /* ---------- Reverse side (gold) ---------- */
  .card-reverse { left: 27px; background: var(--gold); }
  .brand-block {
    position: absolute; top: 30px; left: 0; width: 100%;
    display: flex; align-items: center; justify-content: center; gap: 14px;
  }
  .brand-ring {
    width: 52px; height: 52px; border-radius: 50%;
    border: 4px solid var(--green);
  }
  .brand-name {
    font-weight: 700; font-size: 30px; letter-spacing: 2px;
    color: var(--green); text-transform: uppercase;
  }
  .tagline-band {
    position: absolute; top: 140px; left: 0; width: 100%; height: 34px;
    background: var(--green); color: var(--paper);
    display: flex; align-items: center; justify-content: center;
    font-weight: 700; font-size: 14px; letter-spacing: 1.5px; text-transform: uppercase;
  }
  .office-list {
    position: absolute; top: 192px; left: 20px; right: 20px; bottom: 16px;
    display: grid; grid-template-columns: 1fr 1fr 1fr;
  }
  .office {
    padding: 0 12px; color: var(--paper);
    font-weight: 700; font-size: 11.5px; line-height: 1.55;
  }
  .office + .office { border-left: 1px solid rgba(255,255,255,.85); }
  .office-city {
    color: var(--green); font-size: 14px; letter-spacing: 1px;
    text-transform: uppercase; display: inline-block;
    border-bottom: 1px solid var(--paper); margin-bottom: 5px; padding-bottom: 1px;
  }
  .office-phone { display: flex; align-items: center; gap: 5px; }
  .office-phone svg { width: 11px; height: 11px; fill: var(--green); }

  /* ---------- Front side (white) ---------- */
  .card-front { left: 613px; background: var(--paper); }
  .front-brand {
    position: absolute; left: 20px; top: 48px; width: 215px;
    display: flex; flex-direction: column; align-items: center; gap: 16px;
  }
  .front-brand .brand-ring {
    width: 92px; height: 92px; border: 5px solid var(--gold);
  }
  .front-brand .brand-name { font-size: 22px; letter-spacing: 1px; text-align: center; line-height: 1.15; }
  .divider {
    position: absolute; left: 250px; top: 34px; width: 3px; height: 198px;
    background: var(--green);
  }
  .person {
    position: absolute; left: 272px; top: 28px; right: 14px;
    color: var(--ink); font-weight: 700;
  }
  .person-name {
    color: var(--gold); font-size: 29px; letter-spacing: 1px;
    text-transform: uppercase; line-height: 1.05;
  }
  .person-role { font-size: 13px; line-height: 1.3; margin-top: 4px; }
  .person-address { font-size: 13px; line-height: 1.3; margin-top: 12px; }
  .contact-list { list-style: none; margin-top: 12px; font-size: 13px; line-height: 1.38; }
  .contact-list li { display: flex; align-items: center; gap: 8px; }
  .contact-list svg { width: 12px; height: 12px; fill: none; stroke: var(--gold-deep); stroke-width: 2; flex: none; }
  .front-swoosh {
    position: absolute; left: 0; bottom: 0; width: 560px; height: 90px;
  }
</style>
</head>
<body>
<main class="canvas">

  <section class="card card-reverse" aria-label="Business card reverse side">
    <div class="brand-block">
      <span class="brand-ring" aria-hidden="true"></span>
      <span class="brand-name">Harrowgate Legal</span>
    </div>

    <div class="tagline-band">Clear Advice. Trusted Counsel. Every Step</div>

    <div class="office-list">
      <div class="office">
        <span class="office-city">Melbourne</span>
        <div>Level 12, 88 Wattle Street</div>
        <div>MELBOURNE VIC 3000</div>
        <div class="office-phone">
          <svg viewBox="0 0 24 24" aria-hidden="true"><path d="M6.6 10.8a15.1 15.1 0 0 0 6.6 6.6l2.2-2.2a1 1 0 0 1 1-.25 11.4 11.4 0 0 0 3.6.57 1 1 0 0 1 1 1V20a1 1 0 0 1-1 1A17 17 0 0 1 3 4a1 1 0 0 1 1-1h3.5a1 1 0 0 1 1 1c0 1.25.2 2.45.57 3.57a1 1 0 0 1-.25 1z"/></svg>
          +61 03 9000 2268
        </div>
      </div>
      <div class="office">
        <span class="office-city">Sydney</span>
        <div>Level 9, Marlow House</div>
        <div>21 Quarry Street</div>
        <div>PARRAMATTA NSW 2150</div>
        <div class="office-phone">
          <svg viewBox="0 0 24 24" aria-hidden="true"><path d="M6.6 10.8a15.1 15.1 0 0 0 6.6 6.6l2.2-2.2a1 1 0 0 1 1-.25 11.4 11.4 0 0 0 3.6.57 1 1 0 0 1 1 1V20a1 1 0 0 1-1 1A17 17 0 0 1 3 4a1 1 0 0 1 1-1h3.5a1 1 0 0 1 1 1c0 1.25.2 2.45.57 3.57a1 1 0 0 1-.25 1z"/></svg>
          +61 02 8000 5143
        </div>
      </div>
      <div class="office">
        <span class="office-city">Perth</span>
        <div>Level 18, Banksia Tower</div>
        <div>75 Harbour Terrace</div>
        <div>PERTH, WA 6000</div>
        <div class="office-phone">
          <svg viewBox="0 0 24 24" aria-hidden="true"><path d="M6.6 10.8a15.1 15.1 0 0 0 6.6 6.6l2.2-2.2a1 1 0 0 1 1-.25 11.4 11.4 0 0 0 3.6.57 1 1 0 0 1 1 1V20a1 1 0 0 1-1 1A17 17 0 0 1 3 4a1 1 0 0 1 1-1h3.5a1 1 0 0 1 1 1c0 1.25.2 2.45.57 3.57a1 1 0 0 1-.25 1z"/></svg>
          +61 08 6000 7315
        </div>
      </div>
    </div>
  </section>

  <section class="card card-front" aria-label="Business card front side">
    <div class="front-brand">
      <span class="brand-ring" aria-hidden="true"></span>
      <span class="brand-name">Harrowgate Legal</span>
    </div>

    <span class="divider" aria-hidden="true"></span>

    <div class="person">
      <h1 class="person-name">Daniel Ashford</h1>
      <p class="person-role">Director and Principal Solicitor<br>MBA, Juris Doctor</p>
      <p class="person-address">Suite 310, Kestrel Chambers,<br>58 Bramble Lane,<br>Melbourne VIC 3000</p>
      <ul class="contact-list">
        <li>
          <svg viewBox="0 0 24 24" aria-hidden="true"><path d="M6.6 10.8a15.1 15.1 0 0 0 6.6 6.6l2.2-2.2a1 1 0 0 1 1-.25 11.4 11.4 0 0 0 3.6.57 1 1 0 0 1 1 1V20a1 1 0 0 1-1 1A17 17 0 0 1 3 4a1 1 0 0 1 1-1h3.5a1 1 0 0 1 1 1c0 1.25.2 2.45.57 3.57a1 1 0 0 1-.25 1z"/></svg>
          +61 7 3000 4821
        </li>
        <li>
          <svg viewBox="0 0 24 24" aria-hidden="true"><rect x="6" y="2" width="12" height="20" rx="2"/><line x1="11" y1="18" x2="13" y2="18"/></svg>
          +61 0400 612 397
        </li>
        <li>
          <svg viewBox="0 0 24 24" aria-hidden="true"><circle cx="12" cy="12" r="9"/><path d="M3 12h18M12 3c3 3 3 15 0 18M12 3c-3 3-3 15 0 18"/></svg>
          www.harrowgatelegal.com.au
        </li>
        <li>
          <svg viewBox="0 0 24 24" aria-hidden="true"><rect x="3" y="5" width="18" height="14" rx="1"/><path d="M3 6l9 7 9-7"/></svg>
          daniel@harrowgatelegal.com.au
        </li>
      </ul>
    </div>

    <svg class="front-swoosh" viewBox="0 0 560 90" preserveAspectRatio="none" aria-hidden="true">
      <path d="M0 55 C 200 66, 400 48, 560 18 L 560 90 L 0 90 Z" fill="var(--green)"/>
      <path d="M250 48 C 380 44, 480 30, 560 10" fill="none" stroke="var(--gold)" stroke-width="3"/>
    </svg>
  </section>

</main>
</body>
</html>
```